Storm Restoration Contractor needs a professional letterhead design

Looking for a professional letterhead design. Not looking for your cheapo MS Word standard ones that are readily available. Dont want it to be cookie cutter look like ones readily available online. We just recently changed our logo and want to freshen up all our documents. Our company handles restoring a property back to a pre-loss condition after a storm damages it. For example, wind, hail, flood, fire losses.

Target Market(s)

Property Owners, Homeowners, Property Owners, Commercial Property Owners, Property Management Companies

Industry/Entity Type

Construction Company

Requirements
Must have
• Professional, Use 1 of 2 logo options
• Storm Restoration, Roofing, Siding, Windows

```html
<!DOCTYPE html>
<html lang="en">
<head>
<meta charset="utf-8">
<title>Northgate Exteriors Letterhead</title>
<link href="https://fonts.googleapis.com/css2?family=Open+Sans:wght@400;600;700&display=swap" rel="stylesheet">
<style>
  :root {
    --backdrop: #e9e9ea;
    --paper: #ffffff;
    --brand-blue: #1f74c0;
    --brand-gray: #4a4b4d;
    --ink: #3b3c3e;
    --ink-soft: #5a5b5e;
    --watermark: #eef1f6;
  }
  * { box-sizing: border-box; margin: 0; padding: 0; }
  html, body {
    width: 1200px; height: 795px; overflow: hidden;
    background: var(--backdrop);
    font-family: "Open Sans", Arial, sans-serif;
  }
  .letterhead {
    position: absolute; left: 340px; top: 30px;
    width: 520px; height: 735px;
    background: var(--paper);
    box-shadow: 0 2px 10px rgba(0,0,0,.12);
    overflow: hidden;
  }
  .watermark-disc {
    position: absolute; left: 170px; top: 150px;
    width: 300px; height: 300px; border-radius: 50%;
    background: var(--watermark);
  }
  .brand {
    position: absolute; left: 42px; top: 44px;
    display: flex; align-items: center; gap: 8px;
  }
  .brand-dot {
    width: 26px; height: 26px; border-radius: 50%;
    background: var(--brand-blue);
  }
  .brand-name {
    font-weight: 700; font-size: 13px; letter-spacing: 1.5px;
    color: var(--brand-blue); text-transform: uppercase;
  }
  .contact {
    position: absolute; right: 40px; top: 40px;
    text-align: right; font-size: 7.5px; line-height: 11px;
    color: var(--ink-soft);
  }
  .social {
    display: inline-flex; gap: 2px; vertical-align: middle; margin-left: 3px;
  }
  .social span {
    width: 6px; height: 6px; border-radius: 50%; background: var(--brand-blue);
  }
  .letter-body {
    position: absolute; left: 42px; top: 150px; width: 420px;
    font-size: 8.4px; line-height: 12px; color: var(--ink);
  }
  .salutation { font-weight: 700; font-size: 10px; margin-bottom: 12px; }
  .letter-body p { margin-bottom: 12px; }
  .signature {
    width: 90px; height: 34px; margin-top: 6px;
    background: linear-gradient(90deg, #f1f1f2, #e4e4e6);
    border-radius: 3px;
  }
  .corner-sweep {
    position: absolute; left: 0; bottom: 0; width: 520px; height: 735px;
  }
</style>
</head>
<body>
  <main class="letterhead">
    <div class="watermark-disc"></div>

    <header>
      <div class="brand">
        <span class="brand-dot"></span>
        <span class="brand-name">Northgate Exteriors</span>
      </div>
      <address class="contact" style="font-style:normal">
        2250 Harbor Lane,<br>
        Riverton, CA 95014<span class="social"><span></span><span></span><span></span><span></span></span><br>
        (555) 014-2287<br>
        (555) 014-2290<br>
        hello@northgateexteriors.com<br>
        www.northgateexteriors.com
      </address>
    </header>

    <section class="letter-body">
      <div class="salutation">Dear Mr. Carter,</div>
      <p>Lorem Ipsum is simply dummy text of the printing and typesetting industry. Lorem Ipsum has been the industry's standard dummy text ever since the 1500s, when an unknown printer took a galley of type and scrambled it to make a type specimen book. It has survived not only five centuries, but also the leap into electronic typesetting, remaining essentially unchanged.</p>
      <p>The standard chunk of Lorem Ipsum used since the 1500s is reproduced below for those interested. Sections 1.10.32 and 1.10.33 from "de Finibus Bonorum et Malorum" by Cicero are also reproduced in their exact original form, accompanied by English versions from the 1914 translation by H. Rackham.</p>
      <p>Lorem Ipsum is simply dummy text of the printing and typesetting industry. Lorem Ipsum has been the industry's standard dummy text ever since the 1500s, when an unknown printer took a galley of type and scrambled it to make a type specimen book. It has survived not only five centuries, but also the leap into electronic typesetting, remaining essentially unchanged. It was popularised in the</p>
      <div class="signature" role="img" aria-label="Handwritten signature"></div>
    </section>

    <svg class="corner-sweep" viewBox="0 0 520 735" aria-hidden="true">
      <path d="M150 735 C 260 640, 380 570, 520 520 L 520 735 Z" fill="var(--brand-gray)"/>
      <path d="M175 735 C 280 650, 390 590, 520 545 L 520 735 Z" fill="var(--paper)"/>
      <path d="M200 735 C 300 640, 400 575, 520 528 L 520 735 Z" fill="var(--brand-blue)"/>
      <path d="M250 735 C 340 670, 430 620, 520 590 L 520 735 Z" fill="var(--paper)"/>
    </svg>
  </main>
</body>
</html>
```